Counseling Practice Business Card

I need a professional looking business card incorporating my new logo that was just completed. Card needs to incorporate my name and title, description of my specialty, my address, my phone number, my fax number, my email and my website URL. I need to be able to choose design on/with different paper colors and textures.
I do not have a lot of business card ideas so I am open to anything but I want bold,sharp, clear card without additional designs other than my logo (see attached file info). I am open to different color backgrounds or paper colors including black. I do not like traditional brackets around area codes in phone number or dashes between numbers in phone number. Am open to other ways of presenting including periods between numbers as appropriate. I do not know enough to know what I like yet but I want card to coordinate and work together with my logo. My practice emphasizes natural mental health interventions so any use of color (with background paper color or the blue and green in my logo) that elicits nature is nice. In addition to black, any natural brown or wood looking background might be desirable also. Most of the offerings so far look very similar and boring.

Target Market(s)

Potential therapy clients and other professionals

Contact Information for Business Card

Card information:
Gerald M. Whitcombe, Ph.D.
Licensed Clinical Psychologist
Integrative Health Coach
4812 Marlowe Ridge Blvd SE
Suite 310
Cedarbrook, GA 30412
(770) 415-2983 phone
(770) 581-4096 fax
drgeraldwhitcombe@quillmarsh.net
brightfernwellness.net

Font styles to use
Serif
Sans Serif
Other font styles liked:
• anything that you think looks crisp, clear and easily readable

Requirements
Must have
• Any color used should coordinate with my logo design (see attached files).
• Card should be printed horizontally so top and bottom are longest sides of rectangle.
• Background color or paper color should complement and highlight logo. Do not like a white background. black, grey, brown or any color my logo would blend well with.
Nice to have
• I would like designer to utilize color to highlight letters/name or phone-fax-web symbols.
• Bottom edge of card could be highlighted if appropriate to an idea.
Should not have
• I would NOT want the card to have a pure white background at all.
• No clear cards.
• Cards should be oriented with long sides on bottom and top, NOT sides. DO NOT LIKE THIS THIN TALL ORIENTATION.

```html
<!DOCTYPE html>
<html lang="en">
<head>
<meta charset="utf-8">
<title>Brightfern Wellness – Business Card</title>
<link rel="stylesheet" href="https://fonts.googleapis.com/css2?family=Roboto:wght@400;500&family=Roboto+Condensed:wght@700&display=swap">
<style>
  :root {
    --backdrop: #c9b8a3;
    --card: #131417;
    --strip: #2a73b8;
    --name-blue: #2a73b8;
    --title-green: #1b6e3a;
    --text-light: #d8d8d8;
    --url-grey: #b9b9b9;
    --icon: #ffffff;
  }
  * { margin: 0; padding: 0; box-sizing: border-box; }
  html, body { width: 1200px; height: 960px; overflow: hidden; }
  body {
    position: relative;
    background: var(--backdrop);
    font-family: "Roboto", Arial, sans-serif;
  }
  .card {
    position: absolute;
    width: 600px;
    height: 343px;
    background: var(--card);
    box-shadow: 0 3px 8px rgba(0,0,0,0.35);
    overflow: hidden;
  }
  .card--front { left: 314px; top: 113px; }
  .card--back { left: 311px; top: 472px; }

  .side-strip {
    position: absolute;
    left: 0; top: 0;
    width: 32px; height: 100%;
    background: var(--strip);
  }
  .icon {
    position: absolute;
    left: 8px;
    width: 16px; height: 16px;
    fill: var(--icon);
  }
  .details {
    position: absolute;
    left: 55px;
    top: 49px;
    color: var(--text-light);
  }
  .holder-name {
    font-family: "Roboto Condensed", "Arial Narrow", sans-serif;
    font-weight: 700;
    font-size: 20px;
    color: var(--name-blue);
    text-transform: uppercase;
    line-height: 22px;
  }
  .holder-title {
    font-weight: 500;
    font-size: 15px;
    color: var(--title-green);
    line-height: 19px;
  }
  .address {
    margin-top: 10px;
    font-size: 14.5px;
    line-height: 18px;
    font-style: normal;
  }
  .contact {
    margin-top: 10px;
    list-style: none;
    font-size: 14.5px;
    line-height: 19.5px;
  }

  .brand {
    position: absolute;
    font-family: "Roboto", Arial, sans-serif;
    font-weight: 500;
    color: var(--name-blue);
    text-align: center;
    line-height: 1.05;
  }
  .brand--front { left: 330px; top: 148px; width: 250px; font-size: 30px; }
  .brand--back { left: 150px; top: 124px; width: 300px; font-size: 44px; }

  .back-url {
    position: absolute;
    left: 0; top: 284px;
    width: 100%;
    text-align: center;
    font-size: 14px;
    letter-spacing: 4.2px;
    color: var(--url-grey);
  }
</style>
</head>
<body>

<section class="card card--front" aria-label="Business card front">
  <div class="side-strip">
    <svg class="icon" style="top:50px" viewBox="0 0 16 16" aria-hidden="true"><circle cx="8" cy="4.5" r="3.5"/><path d="M1 16c0-4 3-6.5 7-6.5s7 2.5 7 6.5z"/></svg>
    <svg class="icon" style="top:121px" viewBox="0 0 16 16" aria-hidden="true"><path d="M8 0a5.5 5.5 0 0 0-5.5 5.5C2.5 10 8 16 8 16s5.5-6 5.5-10.5A5.5 5.5 0 0 0 8 0zm0 8a2.5 2.5 0 1 1 0-5 2.5 2.5 0 0 1 0 5z"/></svg>
    <svg class="icon" style="top:181px" viewBox="0 0 16 16" aria-hidden="true"><path d="M3.6 1l2.3 3.2-1.4 1.7c.8 2 2.6 3.8 4.6 4.6l1.7-1.4L14 11.4 12.7 14C7 14 2 9 2 3.3z"/></svg>
    <svg class="icon" style="top:202px" viewBox="0 0 16 16" aria-hidden="true"><rect x="4" y="1" width="8" height="5"/><rect x="1" y="6" width="14" height="6" rx="1"/><rect x="4" y="10" width="8" height="5" fill="#fff" stroke="#2a73b8" stroke-width="1"/></svg>
    <svg class="icon" style="top:223px" viewBox="0 0 16 16" aria-hidden="true"><rect x="1" y="3" width="14" height="10"/><path d="M1.5 3.5L8 9l6.5-5.5" fill="none" stroke="#2a73b8" stroke-width="1.3"/></svg>
    <svg class="icon" style="top:243px" viewBox="0 0 16 16" aria-hidden="true"><circle cx="8" cy="8" r="7"/><path d="M1 8h14M8 1c-3 3.5-3 10.5 0 14M8 1c3 3.5 3 10.5 0 14" fill="none" stroke="#2a73b8" stroke-width="1"/></svg>
  </div>

  <div class="details">
    <h1 class="holder-name">Gerald M. Whitcombe, Ph.D.</h1>
    <p class="holder-title">Licensed Clinical Psychologist</p>
    <p class="holder-title">Integrative Health Coach</p>
    <address class="address">
      4812 Marlowe Ridge Blvd SE<br>
      Suite 310<br>
      Cedarbrook, GA 30412
    </address>
    <ul class="contact">
      <li>(770) 415-2983</li>
      <li>(770) 581-4096</li>
      <li>drgeraldwhitcombe@quillmarsh.net</li>
      <li>www.brightfernwellness.net</li>
    </ul>
  </div>

  <p class="brand brand--front">Brightfern<br>Wellness</p>
</section>

<section class="card card--back" aria-label="Business card back">
  <p class="brand brand--back">Brightfern<br>Wellness</p>
  <p class="back-url">www.brightfernwellness.net</p>
</section>

</body>
</html>
```